Exciting product design for natural pet treats

We need a design for our stand up doy style pouch that blends well with our current logo and also bold enough to stand out from the crowd.

We have a range of natural, Australian made pet treats and need a generic bag that allows for a sticker to be placed on the bag to idenfity the name, while also allowing a space for another sticker on the back for ingredients.
___
Information for the front is: logo, Australian made and owned, Pet Food Only (this is a small font and should not be hero text), 100% Natural, Visit our web site for more amazing products for your pets, Space for sticker 100 - 150mm x 30mm.
___
Information for the back is: Tailwag Depot is proudly Australian owned and operated. We source all our Tailwag Depot treats from reputable suppliers around Australia.

Our Tailwag Depot treats can be purchased through our online store, where you will find a growing range of other brands and products for your dogs, cats, birds, fish, rabbits, guinea pigs, horses, cows, sheep, chickens and more.

For further information, please visit our web site www.tailwagdepot.com.au or email us directly info@tailwagdepot.com.au.
____
The design will be used on three different bag sizes, so our printer can reduce the design from the largest size, but please keep in mind the sizes are 280mm x 380mm, 190mm x 275mm & 160mm x 230mm.

Target Market(s)

Mostly female, 25 to 65 years of age. Pet Lovers, particuarly focussing on dogs.

Industry/Entity Type

pet industry

Requirements
Must have
• Space for sticker on front for the product name 100mm x 30mm. Also a
Nice to have
• Space for a window.
Should not have
• comical pet images. Does not need an image of a pet. Does not need an image of the food.

```html
<!DOCTYPE html>
<html lang="en">
<head>
<meta charset="utf-8">
<title>Tailwag Depot – Treat Pouch Front and Back</title>
<link href="https://fonts.googleapis.com/css2?family=Lora:wght@700&family=Oswald:wght@300;400&family=Josefin+Sans:wght@400;600&display=swap" rel="stylesheet">
<style>
  :root {
    --teal-bg: #5fb2c2;
    --teal: #4fb0bf;
    --purple: #8048c8;
    --purple-deep: #3e1f6e;
    --white: #ffffff;
    --silhouette: #e4e4e6;
    --silhouette-faint: #f1f1f2;
    --bowl-light: #e9eaec;
    --bowl-mid: #b9bcc1;
    --dash: #9a9a9a;
    --natural-green: #2e8b3e;
    --badge-green: #1d7a3a;
  }
  * { box-sizing: border-box; margin: 0; padding: 0; }
  html, body { width: 968px; height: 1200px; overflow: hidden; }
  body { background: var(--teal-bg); position: relative; }

  .panel {
    position: absolute; top: 252px; width: 440px; height: 696px;
    background: var(--white); overflow: hidden;
  }
  .panel--front { left: 28px; }
  .panel--back { left: 500px; }

  .brand-name {
    font-family: "Lora", Georgia, serif; font-weight: 700;
    color: var(--purple-deep); white-space: nowrap; line-height: 1;
  }
  .brand-dot { border-radius: 50%; border: 3px solid var(--teal); }

  /* front */
  .front-silhouette {
    position: absolute; left: 20px; top: 135px; width: 402px; height: 345px;
    background: var(--silhouette); border-radius: 150px 170px 60px 60px;
  }
  .front-mark { position: absolute; left: 177px; top: 100px; width: 86px; height: 86px; }
  .front-name { position: absolute; left: 0; right: 0; top: 204px; text-align: center; font-size: 40px; }
  .front-tagline {
    position: absolute; left: 0; right: 0; top: 262px; text-align: center;
    font-family: "Josefin Sans", sans-serif; font-size: 16px; color: var(--purple); letter-spacing: .5px;
  }
  .sticker-area {
    position: absolute; border: 2px dashed var(--dash); border-radius: 14px; background: var(--white);
  }
  .front-sticker { left: 109px; top: 292px; width: 226px; height: 138px; }
  .food-bowl {
    position: absolute; left: 39px; top: 457px; width: 332px; height: 173px;
    border-radius: 50% 50% 45% 45% / 38% 38% 62% 62%;
    background: linear-gradient(180deg, var(--bowl-light) 0%, var(--bowl-mid) 100%);
  }
  .front-headline {
    position: absolute; left: 0; right: 20px; top: 576px; text-align: center;
    font-family: "Oswald", sans-serif; font-weight: 400; font-size: 16.5px; line-height: 24px;
    letter-spacing: -.2px; color: var(--purple); text-transform: uppercase;
  }
  .web-pill {
    position: absolute; left: 113px; top: 632px; width: 180px; height: 24px; border-radius: 12px;
    background: var(--teal); color: var(--white); text-align: center;
    font-family: "Josefin Sans", sans-serif; font-weight: 600; font-size: 10.5px; line-height: 26px;
  }
  .natural-badge {
    position: absolute; left: 45px; top: 635px; font-family: "Josefin Sans", sans-serif;
    color: var(--natural-green); font-weight: 600; line-height: 1;
  }
  .natural-badge .pct { font-size: 13px; display: block; }
  .natural-badge .word { font-size: 7.5px; display: block; margin-top: 1px; }
  .made-badge {
    position: absolute; left: 328px; top: 612px; width: 44px; height: 44px;
    background: var(--badge-green); border-radius: 4px;
  }

  /* back */
  .back-silhouette {
    position: absolute; left: 23px; top: 364px; width: 402px; height: 360px;
    background: var(--silhouette-faint); border-radius: 200px 200px 0 0;
  }
  .back-brand {
    position: absolute; left: 0; right: 0; top: 138px;
    display: flex; align-items: center; justify-content: center; gap: 10px;
  }
  .back-brand .brand-dot { width: 56px; height: 56px; }
  .back-brand .brand-name { font-size: 30px; }
  .back-proud {
    position: absolute; left: 0; right: 0; top: 211px; text-align: center;
    font-family: "Josefin Sans", sans-serif; font-weight: 600; font-size: 9px; color: var(--teal); letter-spacing: .3px;
  }
  .back-headline {
    position: absolute; left: 0; right: 0; top: 224px; text-align: center;
    font-family: "Oswald", sans-serif; font-weight: 400; font-size: 17px; line-height: 25px; color: var(--purple);
  }
  .back-label {
    position: absolute; left: 0; right: 0; top: 287px; text-align: center;
    font-family: "Josefin Sans", sans-serif; font-size: 11px; color: var(--teal); letter-spacing: .5px;
  }
  .back-sticker { left: 117px; top: 314px; width: 225px; height: 137px; }
  .back-body {
    position: absolute; left: 44px; right: 44px; top: 460px; text-align: center;
    font-family: "Oswald", sans-serif; font-weight: 300; font-size: 14.5px; line-height: 21px; color: var(--purple);
  }
  .back-info-title {
    position: absolute; left: 0; right: 0; top: 587px; text-align: center;
    font-family: "Oswald", sans-serif; font-weight: 300; font-size: 14.5px; color: var(--teal);
  }
  .back-info {
    position: absolute; left: 20px; right: 20px; top: 608px; text-align: center;
    font-family: "Oswald", sans-serif; font-weight: 300; font-size: 13.5px; line-height: 21px; color: var(--purple);
  }
</style>
</head>
<body>
  <section class="panel panel--front" aria-label="Pouch front">
    <div class="front-silhouette" role="img" aria-label="Soft grey silhouette of a seated cat and dog"></div>
    <div class="front-mark brand-dot"></div>
    <div class="front-name brand-name">Tailwag Depot</div>
    <div class="front-tagline">PET FOOD ONLY</div>
    <div class="sticker-area front-sticker" aria-label="Product name sticker area"></div>
    <div class="food-bowl" role="img" aria-label="Steel bowl filled with dry pet treats"></div>
    <p class="front-headline">Visit our web site for more<br>amazing products for your pets</p>
    <div class="natural-badge"><span class="pct">100%</span><span class="word">NATURAL</span></div>
    <div class="web-pill">WWW.TAILWAGDEPOT.COM.AU</div>
    <div class="made-badge" role="img" aria-label="Australian made and owned badge"></div>
  </section>

  <section class="panel panel--back" aria-label="Pouch back">
    <div class="back-silhouette" role="img" aria-label="Faint outline of a rabbit and dog inside a circle"></div>
    <div class="back-brand">
      <span class="brand-dot"></span>
      <span class="brand-name">Tailwag Depot</span>
    </div>
    <div class="back-proud">PROUDLY AUSTRALIAN OWNED AND OPERATED</div>
    <p class="back-headline">WE SOURCE ALL OUR TAILWAG DEPOT TREATS FROM<br>REPUTABLE SUPPLIERS AROUND AUSTRALIA.</p>
    <div class="back-label">INGREDIENTS:</div>
    <div class="sticker-area back-sticker" aria-label="Ingredients sticker area"></div>
    <p class="back-body">OUR TAILWAG DEPOT TREATS CAN BE PURCHASED THROUGH OUR ONLINE STORE, WHERE YOU WILL FIND A GROWING RANGE OF OTHER BRANDS AND PRODUCTS FOR YOUR DOGS, CATS, BIRDS, FISH, RABBITS, GUINEA PIGS, HORSES, COWS, SHEEP, CHICKENS AND MORE.</p>
    <div class="back-info-title">FOR FURTHER INFORMATION:</div>
    <p class="back-info">PLEASE VISIT OUR WEB SITE WWW.TAILWAGDEPOT.COM.AU OR<br>EMAIL US DIRECTLY INFO@TAILWAGDEPOT.COM.AU.</p>
  </section>
</body>
</html>
```